Under Morning Lantern website

I need a website to sell my t-shirt designs. I have around 5 designs I plan to sell on my initial launch, but only 3 photos at the moment. I would love a main page with the product images below maybe a large nicely designed header image, showing products with their sizes, item name/description, a way to add to cart and a review system like stars below each product image. Maybe a share option to Snapwall, Plaza, Wren, Corkboard, etc. would be cool too. Also on the main page under the product images a section showcasing my Snapwall photos for the company. Then a section where I will include an About Me video from like Reelhouse. Lastly, on the main page an option to join my Mailing List at the footer with links to my Plaza and Snapwall social accounts, links to pages (About Me, Shop, Snapwall page, & Contact Us) as well as Track Order.

The other 4 pages will be for an About Me, which is the video I will make later that will be from Reelhouse. Then the Shop page. Then the Snapwall page showcasing all the photos I plan to use to market the products, and a Contact Us Page.

I plan to possibly connect this to Shopify, so showcasing payment options (Palo, Birch Pay, Wayfarer, etc.) would be nice.

Lastly, I don't plan on doing returns/exchanges so maybe an area showing that would be nice too. ALL SALES FINAL

Mobile Friendly!

1st image is logo and other 4 images are t-shirt designs

Coded - Design and coding required

5+ page

• Separate pages, No Refunds (All Sales Final), Add to Cart, Way to Purchase

```html
<!DOCTYPE html>
<html lang="en">
<head>
<meta charset="utf-8">
<title>Under Morning Lantern — Product</title>
<link href="https://fonts.googleapis.com/css2?family=Poppins:wght@300;400;500;600&family=Roboto:wght@400;500;700&display=swap" rel="stylesheet">
<style>
:root{
  --brand:#00adee;
  --ink:#222222;
  --text:#555555;
  --muted:#9a9a9a;
  --line:#e6e6e6;
  --star:#f39c12;
  --green:#5a9a00;
  --footer:#2b2b2b;
  --tint:#eef7fc;
  --photo:#f3f3f3;
}
*{box-sizing:border-box;margin:0;padding:0}
html,body{width:1200px;height:2338px;overflow:hidden;background:#fff}
body{position:relative;font-family:"Poppins",sans-serif;color:var(--ink)}
.abs{position:absolute}
.site-header{position:absolute;left:0;top:0;width:1200px;height:314px;background:var(--brand);font-family:"Roboto",sans-serif}
.brand-mark{position:absolute;left:118px;top:40px;color:#111;font-family:"Roboto",sans-serif;font-weight:700;font-size:22px;letter-spacing:1px;line-height:1.1;width:190px}
.brand-mark small{display:block;font-size:22px}
.main-nav{position:absolute;left:429px;top:47px;width:343px;height:41px;background:#fff;border-radius:21px;display:flex;align-items:center;justify-content:space-around;padding:0 22px;font-size:14px;color:#666}
.main-nav .active{color:#111;font-weight:500;position:relative}
.main-nav .active::after{content:"";position:absolute;left:50%;bottom:-6px;width:3px;height:3px;margin-left:-1.5px;border-radius:50%;background:#111}
.track{position:absolute;left:953px;top:59px;color:#fff;font-size:14px}
.cart{position:absolute;left:1048px;top:48px}
.page-title{position:absolute;left:0;width:1200px;top:196px;text-align:center;color:#fff;font-size:36px;font-weight:700}
.crumbs{position:absolute;left:0;width:1200px;top:247px;text-align:center;color:rgba(255,255,255,.75);font-size:16px}
.crumbs b{font-weight:400;color:#fff}
.crumbs span{margin:0 14px}
.thumb{position:absolute;left:118px;width:67px;height:70px;background:var(--photo)}
.thumb.on{border:2px solid var(--brand)}
.gallery{position:absolute;left:194px;top:373px;width:485px;height:454px;background:var(--photo)}
.gallery .label{position:absolute;left:26px;top:22px;color:var(--brand);font-size:14px}
.shirt{position:absolute;background:linear-gradient(#fafafa,#e2e2e2)}
.info{position:absolute;left:726px;top:0}
h1.pname{position:absolute;left:726px;top:366px;font-size:33px;font-weight:400;white-space:nowrap}
.stars{color:var(--star);letter-spacing:1px;font-size:13px}
.rate{position:absolute;left:726px;top:415px;font-size:13px;color:#888;white-space:nowrap}
.price{position:absolute;left:726px;top:444px;font-size:30px;color:#333}
.desc{position:absolute;left:726px;top:486px;width:360px;font-size:12.5px;line-height:25px;color:#444}
.opt{position:absolute;left:726px;font-size:13px;font-weight:500;color:#444}
.swatch{position:absolute;width:20px;height:20px;border-radius:50%}
.size{position:absolute;font-size:13px;color:#555;display:flex;align-items:center;gap:8px}
.size i{display:block;width:22px;height:22px;border:1px solid #ccc;border-radius:50%}
.clear{position:absolute;left:850px;top:653px;font-size:11.5px;color:#888}
.qty{position:absolute;left:727px;top:689px;width:56px;height:33px;border:1px solid #ddd;font-size:13px;color:var(--brand);padding:7px 0 0 14px}
.qty .step{position:absolute;right:0;top:0;width:16px;height:31px;border-left:1px solid #ddd;font-size:10px;color:#555;text-align:center;line-height:15px}
.btn{position:absolute;height:33px;color:#fff;font-size:14px;font-weight:500;text-align:center;line-height:33px;letter-spacing:.5px}
.btn.cart-btn{left:793px;top:689px;width:189px;background:var(--brand)}
.btn.buy{left:726px;top:742px;width:255px;background:#333}
.share{position:absolute;left:726px;top:795px;width:144px;height:32px;border:1px solid #ccc;display:flex;justify-content:space-around;align-items:center;font-size:9px;color:#777;padding:0 6px}
.tab{position:absolute;top:890px;font-size:27px;font-weight:600}
.tab.off{left:118px;color:#c4c4c4}
.tab.on{left:320px;color:#222}
.sub-h{position:absolute;font-size:15px;font-weight:500;color:#333}
.overall{position:absolute;left:122px;top:984px;color:var(--green);font-size:27px;font-weight:500}
.overall small{font-size:12px;color:#444;font-weight:400;margin-left:4px}
.bar-row{position:absolute;left:122px;width:500px;height:14px}
.bar-row .stars{position:absolute;left:0;top:-3px;font-size:12px}
.bar-row .track-bar{position:absolute;left:105px;top:4px;width:352px;height:10px;background:#eee;border-radius:2px}
.bar-row .fill{height:100%;background:var(--green)}
.bar-row .pct{position:absolute;left:468px;top:0;font-size:11px;color:#888}
.note{position:absolute;left:658px;top:987px;font-size:12px;color:#444}
.note a{color:#e95b4a;text-decoration:none}
.avatar{position:absolute;left:125px;top:1270px;width:54px;height:54px;border-radius:50%;background:#cfcfcf;overflow:hidden}
.client{position:absolute;left:196px;top:1292px;font-size:12px;color:#444}
.client b{font-weight:500}
.review-text{position:absolute;left:199px;top:1322px;width:860px;font-size:12.5px;line-height:24.5px;color:#666}
.section-title{position:absolute;left:0;width:1200px;text-align:center;font-size:32px;font-weight:400;color:#222}
.card{position:absolute;top:1523px;width:221px;height:323px;border:1px solid var(--line);background:#fff}
.card.hot{border-color:var(--brand);background:var(--tint)}
.card .img{position:absolute;left:34px;top:28px;width:150px;height:160px;background:linear-gradient(#2a2a2a,#0d0d0d)}
.card .img.light{background:linear-gradient(#f4f4f4,#dedede)}
.card .name{position:absolute;left:35px;top:225px;font-size:16px;font-weight:500}
.card .stars{position:absolute;left:35px;top:248px;font-size:12px}
.card .cost{position:absolute;left:35px;top:272px;font-size:17px;font-weight:600}
.icon-btn{position:absolute;left:162px;width:42px;height:42px;border-radius:50%;border:2px solid var(--brand);background:#fff}
.icon-btn.fill{background:var(--brand)}
.news-sub{position:absolute;left:0;width:1200px;top:1956px;text-align:center;font-size:12.5px;color:#555}
.news-field{position:absolute;left:262px;top:2010px;width:676px;height:21px;border-bottom:1px solid #ccc;font-size:10px;color:#aaa;display:flex;justify-content:space-between}
.site-footer{position:absolute;left:0;top:2085px;width:1200px;height:253px;background:var(--footer);color:#bbb;font-size:14px}
.site-footer h4{position:absolute;font-weight:400;color:#fff;font-size:16px}
.site-footer p{position:absolute;line-height:23px}
.divider{position:absolute;top:45px;width:1px;height:145px;background:#444}
.foot-brand{position:absolute;left:842px;top:76px;width:190px;text-align:center;color:var(--brand);font-size:17px;font-weight:600;line-height:1.2}
.foot-social{position:absolute;left:860px;top:145px;display:flex;gap:12px}
.foot-social span{width:14px;height:14px;border-radius:50%;background:#888}
</style>
</head>
<body>

<header class="site-header">
  <div class="brand-mark">U.M.L.<small style="font-size:9px;letter-spacing:1.5px;margin-top:6px">UNDER MORNING LANTERN</small></div>
  <nav class="main-nav"><span>About</span><span class="active">Shop</span><span>Snapwall</span><span>Contact</span></nav>
  <div class="track">Track Order</div>
  <svg class="cart" width="38" height="36" viewBox="0 0 38 36" aria-label="Cart">
    <path d="M2 11h5l4 15h15l3-11H9" fill="none" stroke="#fff" stroke-width="1.8"/>
    <circle cx="13" cy="31" r="2" fill="#fff"/><circle cx="24" cy="31" r="2" fill="#fff"/>
    <circle cx="27" cy="8" r="7.5" fill="#2b2b2b"/>
    <text x="27" y="11.5" fill="#fff" font-size="10" text-anchor="middle" font-family="Roboto,sans-serif">0</text>
  </svg>
  <div class="page-title">PRODUCT NAME</div>
  <div class="crumbs">Home<span>|</span>Shop<span>|</span><b>Product Name</b></div>
</header>

<div class="thumb" style="top:373px" role="img" aria-label="Front view of white t-shirt"></div>
<div class="thumb on" style="top:457px" role="img" aria-label="Back view of white t-shirt with heart print"></div>
<div class="gallery">
  <div class="label">Back Design</div>
  <div class="shirt" style="left:85px;top:48px;width:330px;height:360px;border-radius:40px 40px 6px 6px" role="img" aria-label="White t-shirt, back view, with concentric heart print"></div>
</div>

<h1 class="pname">Product Name</h1>
<div class="rate"><span class="stars">★★★★☆</span> (18 customer review)</div>
<div class="price">$99</div>
<p class="desc">Lorem Ipsum is simply dummy text of the printing and typesetting industry. Lorem Ipsum has been the industry's</p>

<div class="opt" style="top:567px">COLOR</div>
<div class="swatch" style="left:806px;top:565px;background:#8e5bc4"><svg width="20" height="20"><path d="M6 10l3 3 5-6" stroke="#fff" stroke-width="1.5" fill="none"/></svg></div>
<div class="swatch" style="left:843px;top:565px;background:#222"></div>
<div class="swatch" style="left:881px;top:565px;border:1px solid #ccc"></div>
<div class="swatch" style="left:916px;top:565px;background:var(--brand)"></div>
<div class="swatch" style="left:954px;top:565px;background:#26aaa4"></div>

<div class="opt" style="top:620px">SIZE</div>
<div class="size" style="left:806px;top:617px"><i style="display:flex;align-items:center;justify-content:center"><svg width="12" height="10"><path d="M1 5l3 3 7-7" stroke="#555" fill="none"/></svg></i>S</div>
<div class="size" style="left:874px;top:617px"><i></i>M</div>
<div class="size" style="left:943px;top:617px"><i></i>L</div>
<div class="size" style="left:1012px;top:617px"><i></i>XL</div>
<div class="clear">CLEAR</div>

<div class="qty">1<div class="step">+<br>-</div></div>
<div class="btn cart-btn">ADD TO CART</div>
<div class="btn buy">BUY NOW</div>
<div class="share"><span>Wren</span><span>Plaza</span><span>Cork</span><span>Ledger</span></div>

<div class="tab off">Description</div>
<div class="tab on">Reviews (1)</div>

<div class="sub-h" style="left:122px;top:953px">Based On 1 Reviews</div>
<div class="overall">5.00<small>Overall</small></div>
<div class="bar-row" style="top:1030px"><span class="stars">★★★★★</span><div class="track-bar"><div class="fill" style="width:100%"></div></div><span class="pct">100%</span></div>
<div class="bar-row" style="top:1060px"><span class="stars">★★★★☆</span><div class="track-bar"></div><span class="pct" style="left:474px">0%</span></div>
<div class="bar-row" style="top:1090px"><span class="stars">★★★☆☆</span><div class="track-bar"></div><span class="pct" style="left:474px">0%</span></div>
<div class="bar-row" style="top:1120px"><span class="stars">★★☆☆☆</span><div class="track-bar"></div><span class="pct" style="left:474px">0%</span></div>
<div class="bar-row" style="top:1150px"><span class="stars">★☆☆☆☆</span><div class="track-bar"></div><span class="pct" style="left:474px">0%</span></div>

<div class="sub-h" style="left:658px;top:953px">Add A Review</div>
<div class="note">You must be <a>logged in</a> to post a review.</div>

<div class="sub-h" style="left:125px;top:1225px">1 Review For Colorful Jacket</div>
<div class="avatar"><svg width="54" height="54"><circle cx="27" cy="21" r="10" fill="#fff"/><path d="M7 54c2-14 10-19 20-19s18 5 20 19z" fill="#fff"/></svg></div>
<div class="abs stars" style="left:196px;top:1268px">★★★★★</div>
<div class="client"><b>Client Name</b> – January 14, 2020:</div>
<p class="review-text">Lorem Ipsum is simply dummy text of the printing and typesetting industry. Lorem Ipsum has been the industry's standard dummy text ever since the 1500s, when an unknown printer took a galley of type and scrambled it to make a type specimen book. It has survived not only five centuries,</p>

<h2 class="section-title" style="top:1440px">Related Products</h2>
<svg class="abs" style="left:1027px;top:1471px" width="50" height="20"><path d="M8 2l-7 8 7 8" stroke="#555" fill="none" stroke-width="1.5"/><path d="M38 2l7 8-7 8" stroke="var(--brand)" fill="none" stroke-width="1.5"/></svg>

<div class="card" style="left:120px"><div class="img" role="img" aria-label="Black t-shirt with blue lettering print"></div><div class="name">Product Name</div><div class="stars">★★★☆☆</div><div class="cost">$120.00</div></div>
<div class="card hot" style="left:367px"><div class="img" style="left:32px;width:135px" role="img" aria-label="Black t-shirt with blue front print"></div>
  <div class="icon-btn" style="top:22px"><svg width="38" height="38"><path d="M13 25l12-12M13 19v6h6M25 19v-6h-6" stroke="#333" fill="none" stroke-width="1.3"/></svg></div>
  <div class="icon-btn" style="top:76px"><svg width="38" height="38"><path d="M19 26l-6-6a3.5 3.5 0 016-4 3.5 3.5 0 016 4z" stroke="#333" fill="none" stroke-width="1.3"/></svg></div>
  <div class="icon-btn fill" style="top:131px"><svg width="38" height="38"><path d="M11 14h3l2 8h8l2-6h-11" stroke="#fff" fill="none" stroke-width="1.5"/><circle cx="17" cy="25" r="1.3" fill="#fff"/><circle cx="23" cy="25" r="1.3" fill="#fff"/></svg></div>
  <div class="name">Product Name</div><div class="stars">★★★★☆</div><div class="cost">$120.00</div></div>
<div class="card" style="left:614px"><div class="img light" role="img" aria-label="Two white t-shirts, front and back with heart print"></div><div class="name">Product Name</div><div class="stars">★★★★★</div><div class="cost">$120.00</div></div>
<div class="card" style="left:861px"><div class="img" style="top:36px;height:150px" role="img" aria-label="Black t-shirt with purple front print"></div><div class="name">Product Name</div><div class="stars">★★★★☆</div><div class="cost">$120.00</div></div>

<h2 class="section-title" style="top:1910px">Join Our Newsletter</h2>
<div class="news-sub">Sale up to 20% off for your next purchase in this month!</div>
<div class="news-field"><span>Your email address</span><span>Subscribe</span></div>

<footer class="site-footer">
  <h4 style="left:154px;top:42px">Contact Us</h4>
  <p style="left:154px;top:82px;width:180px">Lorem Ipsum, is simply dummy text of the</p>
  <p style="left:154px;top:145px">+xxx xxxx xxxxx</p>
  <p style="left:154px;top:177px">xxxxxxx@mailbox.com</p>
  <div class="divider" style="left:402px"></div>
  <h4 style="left:530px;top:43px">Contact Us</h4>
  <p style="left:530px;top:83px;line-height:24.5px">Home<br>About<br>Services<br>Contact<br>Track Order</p>
  <div class="divider" style="left:733px"></div>
  <div class="foot-brand">U.M.L.<br><span style="font-size:9px;letter-spacing:1.5px">UNDER MORNING LANTERN</span></div>
  <div class="foot-social" aria-label="Social links"><span></span><span></span><span></span><span></span><span></span></div>
</footer>

</body>
</html>
```